Heron Loan Partners Business Card

We need a business card design for our mortgage servicing company. In addition to servicing the loans of homeowners, we help homeowners with purchasing their homes and any mortgage refinancing. We would like to see designs that use the colors in the logo attached below (gold-ish yellow and navy blue), and any other design you deem fit! The design should communicate a simpler life with smart mortgages provided by Heron.

```html
<!DOCTYPE html>
<html lang="en">
<head>
<meta charset="utf-8">
<title>Heron Loan Partners Business Card</title>
<link rel="stylesheet" href="https://fonts.googleapis.com/css2?family=Open+Sans:wght@400;600;700&display=swap">
<style>
  :root {
    --gold: #e2b33c;
    --navy: #231d5c;
    --ink: #1c1c22;
    --paper: #ffffff;
    --backdrop: #e9e9ec;
  }
  * { box-sizing: border-box; margin: 0; padding: 0; }
  html, body { width: 1200px; height: 780px; overflow: hidden; }
  body {
    background: var(--backdrop);
    font-family: "Open Sans", Arial, sans-serif;
    color: var(--ink);
    display: flex;
    align-items: center;
    justify-content: center;
    gap: 40px;
  }
  .card {
    position: relative;
    width: 540px;
    height: 310px;
    border-radius: 16px;
    overflow: hidden;
    box-shadow: 0 10px 30px rgba(0,0,0,0.18);
  }
  .card-front { background: var(--paper); }
  .card-back {
    background: var(--gold);
    display: flex;
    align-items: center;
    justify-content: center;
  }
  .brand-name {
    position: absolute;
    left: 40px;
    top: 28px;
    font-size: 40px;
    font-weight: 700;
    color: var(--gold);
    letter-spacing: 0.5px;
  }
  .contact-list {
    position: absolute;
    left: 40px;
    top: 108px;
    list-style: none;
    font-size: 13px;
    line-height: 22px;
  }
  .contact-list li { display: flex; align-items: center; gap: 8px; }
  .contact-icon { width: 12px; height: 12px; flex: none; }
  .holder {
    position: absolute;
    right: 40px;
    top: 130px;
    text-align: right;
  }
  .holder-name {
    font-size: 27px;
    font-weight: 700;
    line-height: 1.1;
  }
  .holder-name .first { color: var(--gold); }
  .holder-name .last { color: var(--navy); }
  .holder-title {
    font-size: 15px;
    font-weight: 400;
    margin-top: 2px;
  }
  .divider {
    position: absolute;
    left: 40px;
    right: 40px;
    top: 200px;
    height: 1.5px;
    background: var(--ink);
  }
  .accent-tab {
    position: absolute;
    right: 0;
    top: 182px;
    width: 22px;
    height: 36px;
    background: var(--gold);
  }
  .address {
    position: absolute;
    right: 40px;
    bottom: 28px;
    text-align: right;
    font-size: 15px;
    line-height: 22px;
  }
  .back-mark {
    font-size: 30px;
    font-weight: 700;
    color: var(--paper);
  }
</style>
</head>
<body>
  <section class="card card-front" aria-label="Card front">
    <div class="brand-name">Heron</div>

    <ul class="contact-list">
      <li>
        <svg class="contact-icon" viewBox="0 0 12 12" aria-hidden="true"><path d="M2.5 1 L4.5 1 L5.2 3.4 L4 4.4 Q5 6.9 7.6 8 L8.6 6.8 L11 7.5 L11 9.5 Q11 11 9.5 11 Q1 10 1 2.5 Q1 1 2.5 1 Z" fill="var(--gold)"/></svg>
        (555) 214-0386
      </li>
      <li>
        <svg class="contact-icon" viewBox="0 0 12 12" aria-hidden="true"><rect x="0.5" y="2" width="11" height="8" rx="1" fill="var(--gold)"/><path d="M1 2.8 L6 6.6 L11 2.8" stroke="#fff" stroke-width="1" fill="none"/></svg>
        hello@heronloan.example
      </li>
      <li>
        <svg class="contact-icon" viewBox="0 0 12 12" aria-hidden="true"><circle cx="6" cy="6" r="5.3" fill="var(--gold)"/><path d="M0.8 6 H11.2 M6 0.8 Q2.8 6 6 11.2 M6 0.8 Q9.2 6 6 11.2" stroke="#fff" stroke-width="0.8" fill="none"/></svg>
        www.heronloan.example
      </li>
    </ul>

    <div class="holder">
      <div class="holder-name"><span class="first">Dana</span> <span class="last">Whitfield</span></div>
      <div class="holder-title">Managing Director</div>
    </div>

    <div class="divider"></div>
    <div class="accent-tab"></div>

    <address class="address" style="font-style: normal;">
      1840 Lakeshore Ave. Suite 310<br>
      Riverton, TX 75001
    </address>
  </section>

  <section class="card card-back" aria-label="Card back">
    <div class="back-mark">Heron</div>
  </section>
</body>
</html>
```